Tally Roster survey and prize

We need an A4 poster design for a survey and competition I wish to hold. The survey will be on Poll Heron. My website www.TallyRoster.com.au will redirect the users to the survey page. I will be selecting a survey entrant at random to win a prize. The prize is $200 cash. The survey will be open for two months as the mail out of this poster will go throughout Victoria, Australia. The competition end date is yet to be decided - depends on when I can get this poster completed and the mail out done.

The mail out is targeting the Aged Care industry workers and decision makers. It hopefully will be placed on a notice board in the facilities and need to attract attention for people to visit my site and then take the survey.

The survey is for not for residents but for the workers in the facility.

Reason: Just got some feedback on required content of the poster. Text for the poster required: "The survey is for determining a market for rostering and payroll software, your assitance in taking this survey would be greatly appreciated." Martin Holloway

Target Market(s)

Workers in Aged Care industry and decision makers.

Industry/Entity Type

Industry

Requirements
Must have
• 1. Must reference the website www.TallyRoster.com.au.
2. Must mention that there is a prize of $200.
3. Must mention that entry to the competition is dependant on taking the survey.
4. Must mention the close date (date yet to be decided).
5. Must mention winning contestant will be contacted by phone.

```html
<!DOCTYPE html>
<html lang="en">
<head>
<meta charset="utf-8">
<title>Tally Roster – Survey Competition Poster</title>
<link rel="stylesheet" href="https://fonts.googleapis.com/css2?family=League+Gothic&family=Archivo+Black&family=Arimo:wght@400;700&display=swap">
<style>
  :root {
    --ink: #363a45;
    --blue: #3e5f9f;
    --yellow: #f6d447;
    --white: #ffffff;
    --paper: #ffffff;
    --body-text: #111111;
  }
  html, body {
    margin: 0;
    padding: 0;
    overflow: hidden;
    background: var(--paper);
  }
  .poster {
    position: relative;
    width: 848px;
    height: 1200px;
    overflow: hidden;
    background: var(--paper);
    font-family: "Arimo", Arial, sans-serif;
  }
  .hero-photo {
    position: absolute;
    left: 0;
    top: 0;
    width: 577px;
    height: 955px;
    background:
      radial-gradient(ellipse at 30% 10%, #8a9a5c 0%, transparent 45%),
      radial-gradient(ellipse at 75% 35%, #e7b8c4 0%, transparent 40%),
      radial-gradient(ellipse at 35% 50%, #b9cfe6 0%, transparent 45%),
      linear-gradient(180deg, #7d8a55 0%, #a89a7d 45%, #9a9c9c 75%, #c9c8c2 100%);
  }
  .headline {
    position: absolute;
    left: 0;
    top: 0;
    width: 848px;
    height: 720px;
    font-family: "League Gothic", "Oswald", sans-serif;
  }
  .headline .dark { fill: var(--ink); }
  .headline .accent { fill: var(--blue); }
  .headline .rule { stroke: var(--blue); stroke-width: 2; }

  .survey-box {
    position: absolute;
    left: 50px;
    top: 762px;
    width: 349px;
    height: 261px;
    border-radius: 34px;
    background: var(--ink);
    color: var(--white);
    text-align: center;
  }
  .survey-box__intro {
    margin: 52px 0 0;
    font-size: 29px;
    line-height: 35px;
  }
  .survey-box__url {
    margin: 42px 0 0;
    font-size: 23px;
    color: var(--white);
  }

  .prize-badge {
    position: absolute;
    left: 468px;
    top: 731px;
    width: 390px;
    height: 390px;
  }
  .prize-badge .win,
  .prize-badge .amount {
    font-family: "Archivo Black", "Arial Black", sans-serif;
    fill: var(--white);
  }
  .prize-badge .cash {
    font-family: "Archivo Black", "Arial Black", sans-serif;
    fill: var(--ink);
  }

  .closing {
    position: absolute;
    left: 58px;
    top: 1062px;
    width: 470px;
    color: var(--body-text);
  }
  .closing__date {
    margin: 0;
    font-size: 31px;
    font-weight: 700;
  }
  .closing__date span {
    font-weight: 400;
  }
  .closing__note {
    margin: 6px 0 0;
    font-size: 17px;
  }
  .closing__purpose {
    margin: 5px 0 0;
    font-size: 12.5px;
    line-height: 15px;
    color: var(--ink);
  }

  .footer-band {
    position: absolute;
    left: 0;
    bottom: 0;
    width: 848px;
    height: 34px;
    background: var(--blue);
    color: var(--white);
    font-size: 17px;
    line-height: 34px;
    text-align: center;
  }
</style>
</head>
<body>
<main class="poster">
  <div class="hero-photo" role="img" aria-label="Photo of an older couple in a garden, the man in a cap using a laptop while the woman leans on his shoulders smiling"></div>

  <svg class="headline" viewBox="0 0 848 720" aria-label="Take the survey, enter the competetion, become the winner">
    <text class="dark" x="584" y="135" font-size="124" textLength="250" lengthAdjust="spacingAndGlyphs">TAKE THE</text>
    <text class="accent" x="584" y="278" font-size="182" textLength="250" lengthAdjust="spacingAndGlyphs">SURVEY</text>
    <text class="dark" x="584" y="385" font-size="126" textLength="250" lengthAdjust="spacingAndGlyphs">ENTER THE</text>
    <text class="accent" x="584" y="470" font-size="105" textLength="250" lengthAdjust="spacingAndGlyphs">COMPETETION</text>
    <text class="dark" x="584" y="606" font-size="164" textLength="250" lengthAdjust="spacingAndGlyphs">BECOME</text>
    <line class="rule" x1="584" y1="616" x2="834" y2="616"/>
    <text class="accent" x="584" y="705" font-size="105" textLength="250" lengthAdjust="spacingAndGlyphs">THE WINNER</text>
  </svg>

  <section class="survey-box">
    <p class="survey-box__intro">Complete our<br>online survey at</p>
    <p class="survey-box__url">www.TallyRoster.com.au</p>
  </section>

  <svg class="prize-badge" viewBox="0 0 390 390" aria-label="Win $200 cash">
    <defs>
      <clipPath id="badge-clip"><circle cx="195" cy="195" r="185"/></clipPath>
      <filter id="text-shadow" x="-10%" y="-10%" width="130%" height="130%">
        <feDropShadow dx="3" dy="4" stdDeviation="2" flood-color="#1c2a48" flood-opacity="0.55"/>
      </filter>
    </defs>
    <g clip-path="url(#badge-clip)">
      <rect width="390" height="390" fill="var(--blue)"/>
      <polygon points="0,345 390,250 390,390 0,390" fill="var(--yellow)"/>
    </g>
    <g transform="rotate(-11 195 195)" filter="url(#text-shadow)">
      <text class="win" x="190" y="165" font-size="92" text-anchor="middle">WIN</text>
      <text class="amount" x="200" y="255" font-size="112" text-anchor="middle">$200</text>
    </g>
    <text class="cash" x="240" y="348" font-size="38" text-anchor="middle" transform="rotate(-13 240 335)">CASH</text>
  </svg>

  <section class="closing">
    <p class="closing__date">Closing Date <span>xx-xx-xxxx</span></p>
    <p class="closing__note">Winning Contestant will be Informed by Phone</p>
    <p class="closing__purpose">The survey is for determining a market for rostering and payroll software, your assistance in taking this survey would be greatly appreciated.</p>
  </section>

  <footer class="footer-band">Winning Contestant will be Informed by Phone</footer>
</main>
</body>
</html>
```